Wordpress Theme for Carewell Health

** Please view updated Sitemap2.pdf doc to clarify some confusion ***

This is a multiuser WordPress subscription site for Carewell Health. Please see attachment for sitemap. Please do not include extra content like social media icons, search bars, or images. If you have questions, please ask for clarification.
The site contains the following pages and sub-pages:

1. Home
2. Our Clinic
2a. Our Clinic > Mission
2b. Our Clinic > Services
2c. Our Clinic > Clinic Policies
2d. Our Clinic > Schedules
3. Our Staff
3a. Our Staff > [Staff member page]
4. Resources
4a. Resources > Patient Health (index)
4b. Resources > Patient Health (index) > [post]
4c. Resources > Links
4d. Resources > Forms
5. Alerts
5a. Alerts > [Alert Page]
6. Contact Us

Includes the Following Pages, Subpages, and Content
1. Home
a. About Us
b. Our Staff
c. Bulletins
d. Accepting New Patients (shown as an alert widget)
e. Links
i. Physician Toolbox
ii. Book an Appointment
f. Clinic Policies
i. Show first 3 policies (e.g. Late Arrivals, Missed Appointments, Fees)
ii. Link to Clinic Policies page
g. Primary widget (displayed on all pages)
i. Hours of operation
ii. Contact Info
1. Tel
2. Fax
3. Email
4. Address
5. Get directions (link to Google Maps)
2. Our Clinic
a. Main Page
i. Clinic Name
ii. Overview
iii. Languages Spoken
iv. Secondary Navigation
1. Mission
2. Services
3. Clinic Policies
4. Schedules (see attachment)
b. Our Clinic > Mission
c. Our Clinic > Services
i. For each service include service TITLE and DESCRIPTION
d. Our Clinic > Clinic Policies
i. For each policy include policy TITLE and DESCRIPTION
ii. Include the following policies in mockup
1. Late arrivals
2. Missed appointments
3. Fees for missed appointments
4. Referrals and follow-ups
5. Services not covered by RDA
6. Information for LTF patients
7. Medical Legal Reports
e. Our Clinic > Schedules
3. Our Staff
a. Main Page
i. Display a list of staff members. Include NAME and DESIGNATION
b. Our Staff > [Staff Name]
i. Include NAME, PICTURE, DESIGNATION, and BIO
4. Resources
a. Resources > Patient Health
i. Main Page
1. Posts (ordered by date)
a. Title
b. Summary
2. Side Navigation
a. Post Categories
ii. Patient Health > [post title]
1. Title
2. Post Category
3. Date
4. Author
5. Summary
6. Body
b. Resources > Links
1. Secondary Navigation - Categories
a. Sample Categories:
i. Local Services
ii. RDA and Drug Coverage
iii. Mental Health Resources
2. Category page
a. Include the following links in the 'Local Services' category
i. Hypertension clinics
ii. Home Care services
iii. Vaccine Clinics
c. Resources > Forms
i. Display a table with form TITLE and CATEGORY
ii. Side Navigation
1. Form Categories
a. Use the following sample Categories
i. Referrals
ii. Insurance
iii. Intake
iv. Discharge
v. Waivers
5. Alerts
a. Main page
i. List of all Alert posts
1. Include post TITLE as a link to the post
ii. Side Navigation
1. Alerts Archive
a. shown as Month + Number of posts
iii. Alerts > [Alert page]
1. Include TITLE, DATE, AUTHOR, BODY
6. Contact Us
a. Map
b. Hours of operation
c. Address
d. Phone number
e. Fax number
e. Fax number
f. Map
g. Email

Design notes:
- fixed width
- responsive (need designs for mobile, tablet, and desktop)
- simple, dark font, white background
- use Font Awesome icons where needed
- user adds own logo

Target Market(s)

Carewell Health

Industry/Entity Type

Medical

Number of Pages Required

5+ page

Font styles to use
Serif
Sans Serif

Requirements
Must have
• Please keep designs very simple.
• Examples:
• https://www.quolbin.com/install
• http://www.ventrohax.com/company/about-us
• http://brindlequota.org/
• http://www.trosk.com/
Should not have
• Minimal or no use of shadows and gradients

```html
<!DOCTYPE html>
<html lang="en">
<head>
<meta charset="utf-8">
<title>Schedule – Carewell Health</title>
<link rel="stylesheet" href="https://fonts.googleapis.com/css2?family=Open+Sans:wght@400;600;700&display=swap">
<style>
:root{
  --blue:#0a86d8;
  --sky:#3cb0f5;
  --ink:#333;
  --band:#f7f7f7;
  --row:#f5f5f5;
  --line:#e2e2e2;
  --footer:#262626;
  --footer-text:#8c8c8c;
  --footer-light:#ddd;
  --white:#fff;
}
*{box-sizing:border-box;margin:0;padding:0}
html,body{width:1200px;height:698px;overflow:hidden;background:var(--white);font-family:"Open Sans",Arial,sans-serif;color:var(--ink)}
a{color:inherit;text-decoration:none}
ul{list-style:none}
.wrap{width:876px;margin-left:162px;position:relative}

.topbar{height:30px;background:var(--blue);color:var(--white);font-size:9.5px}
.topbar .wrap{display:flex;justify-content:space-between;align-items:center;height:30px}
.topbar .sep{border-left:1px solid var(--white);margin:0 5px;height:15px;display:inline-block;vertical-align:middle}

.header{height:83px}
.header .wrap{display:flex;justify-content:space-between;height:83px}
.brand{display:flex;align-items:center;gap:14px;font-weight:600;font-size:20px;color:var(--ink)}
.brand-dot{width:20px;height:20px;border-radius:50%;background:var(--blue);flex:none}
.main-nav{display:flex;font-size:10.5px;margin-right:8px}
.main-nav a{display:flex;align-items:center;height:83px;padding:0 19px}
.main-nav a:first-child{padding-left:0}
.main-nav a:last-child{padding-right:0}
.main-nav a.active{background:var(--blue);color:var(--white);padding:0 7px;margin:0 14px}

.page-head{height:59px;background:var(--band);padding-top:15px}
.page-title{font-size:10.5px;font-weight:700}
.crumbs{font-size:9.5px;margin-top:4px}

.content{display:flex;padding-top:45px;height:283px}
.side{width:202px}
.side h3{font-size:10.5px;font-weight:700;padding-bottom:4px;border-bottom:1px solid #ccc}
.side ul{font-size:10px;padding-left:14px;padding-top:2px}
.side li{line-height:22.5px}
.side li.current{color:var(--blue);font-weight:700}
.main{margin-left:23px;width:652px}
.main h2{font-size:13px;font-weight:700;letter-spacing:.3px;margin-top:-4px}
.schedule{width:652px;border-collapse:collapse;margin-top:6px;font-size:10px;border:1px solid var(--line);table-layout:fixed}
.schedule th{background:var(--sky);color:var(--white);font-size:8.5px;font-weight:700;height:25px;border-left:1px solid rgba(255,255,255,.5);width:42.7px}
.schedule th:first-child{border-left:0;width:353px}
.schedule td{height:22.5px;border-left:1px solid var(--line);text-align:center}
.schedule td:first-child{text-align:left;padding-left:14px;border-left:0}
.schedule tr:nth-child(odd) td{background:var(--row)}
.tick{width:9px;height:8px;vertical-align:middle}

.footer{border-top:4px solid var(--blue);background:var(--footer);height:206px;color:var(--footer-text);font-size:10px}
.footer .wrap{display:flex;padding-top:29px}
.f-brand{width:299px;padding-top:10px}
.f-brand .brand{color:var(--white);font-size:20px}
.f-brand p{color:var(--footer-light);font-size:9px;line-height:13.5px;margin-top:19px;width:205px}
.footer h4{font-size:12px;font-weight:600;color:#9a9a9a;margin-bottom:6px}
.f-nav{width:149px}
.f-nav li{line-height:18px}
.f-nav li:first-child{color:var(--footer-light)}
.f-hours{width:226px}
.f-hours dl,.f-contact dl{display:grid;line-height:18px}
.f-hours dl{grid-template-columns:91px auto}
.f-contact dl{grid-template-columns:91px auto;line-height:15px;margin-top:-2px}
.bottom{height:37px;background:var(--footer);border-top:1px solid #444;color:var(--footer-text);font-size:10px}
.bottom .wrap{display:flex;align-items:center;height:34px}
.bottom .legal{margin-left:105px;display:flex;gap:26px}
.bottom .credit{margin-left:auto}
</style>
</head>
<body>
<svg width="0" height="0" style="position:absolute">
  <symbol id="tick" viewBox="0 0 10 8"><path d="M1 4.2 3.8 7 9 1" fill="none" stroke="#9a9a9a" stroke-width="1.8"/></symbol>
</svg>

<div class="topbar"><div class="wrap">
  <span>To help Here : 111 444 7777<span class="sep"></span>Email : Hello@ Carewell.ca</span>
  <span><a href="#">Book an Appointment</a><span class="sep"></span><a href="#">Physician Toolbox</a></span>
</div></div>

<header class="header"><div class="wrap">
  <a class="brand" href="#"><span class="brand-dot"></span>Carewell Health</a>
  <nav class="main-nav">
    <a href="#">Home</a><a class="active" href="#">Our Clinic</a><a href="#">Our Staff</a><a href="#">Resources</a><a href="#">Alerts</a><a href="#">Contact Us</a>
  </nav>
</div></header>

<section class="page-head"><div class="wrap">
  <h1 class="page-title">SCHEDULE</h1>
  <div class="crumbs">HOME / OUR CLINIC / SCHEDULE</div>
</div></section>

<section class="wrap content">
  <aside class="side">
    <h3>OUR CLINIC</h3>
    <ul><li>About</li><li>Misssion</li><li>Services</li><li>Policies</li><li class="current">Schedules</li></ul>
  </aside>
  <div class="main">
    <h2>SCHEDULE</h2>
    <table class="schedule">
      <tr><th></th><th>MON</th><th>TUE</th><th>WED</th><th>THU</th><th>FRI</th><th>SAT</th><th>SUN</th></tr>
      <tr><td>Dr. Laura Penfold</td><td><svg class="tick"><use href="#tick"/></svg></td><td></td><td><svg class="tick"><use href="#tick"/></svg></td><td><svg class="tick"><use href="#tick"/></svg></td><td><svg class="tick"><use href="#tick"/></svg></td><td></td><td><svg class="tick"><use href="#tick"/></svg></td></tr>
      <tr><td>Dr. Owen Hartley</td><td><svg class="tick"><use href="#tick"/></svg></td><td><svg class="tick"><use href="#tick"/></svg></td><td><svg class="tick"><use href="#tick"/></svg></td><td></td><td><svg class="tick"><use href="#tick"/></svg></td><td><svg class="tick"><use href="#tick"/></svg></td><td></td></tr>
      <tr><td>Dr. Miles Carrow</td><td><svg class="tick"><use href="#tick"/></svg></td><td></td><td><svg class="tick"><use href="#tick"/></svg></td><td><svg class="tick"><use href="#tick"/></svg></td><td></td><td></td><td></td></tr>
      <tr><td>Dr. Peter Vandell</td><td></td><td><svg class="tick"><use href="#tick"/></svg></td><td></td><td><svg class="tick"><use href="#tick"/></svg></td><td></td><td></td><td></td></tr>
      <tr><td>Dr. Ethan Roswell</td><td><svg class="tick"><use href="#tick"/></svg></td><td><svg class="tick"><use href="#tick"/></svg></td><td><svg class="tick"><use href="#tick"/></svg></td><td></td><td><svg class="tick"><use href="#tick"/></svg></td><td></td><td><svg class="tick"><use href="#tick"/></svg></td></tr>
    </table>
  </div>
</section>

<footer class="footer"><div class="wrap">
  <div class="f-brand">
    <div class="brand"><span class="brand-dot"></span>Carewell Health</div>
    <p>Lorem Ipsum is simply dummy text of the printing and typesetting industry. Lorem Ipsum has been the industry's standard dummy text</p>
  </div>
  <div class="f-nav">
    <h4>Navigation</h4>
    <ul><li>Home</li><li>Our Clinic</li><li>Newsletter</li><li>Our Staff</li><li>Resources</li></ul>
  </div>
  <div class="f-hours">
    <h4>Hours of Opration</h4>
    <dl>
      <dt>Monday :</dt><dd>8:00 AM - 6:00 PM</dd>
      <dt>Tuesday :</dt><dd>8:00 AM - 6:00 PM</dd>
      <dt>Wednesday :</dt><dd>8:00 AM - 6:00 PM</dd>
      <dt>Thursday :</dt><dd>8:00 AM - 6:00 PM</dd>
      <dt>Friday :</dt><dd>8:00 AM - 6:00 PM</dd>
      <dt>Saturday :</dt><dd>9:00 AM - 4:00 PM</dd>
      <dt>Sunday :</dt><dd>9:00 AM - 4:00 PM</dd>
    </dl>
  </div>
  <div class="f-contact">
    <h4>Contact Us</h4>
    <dl>
      <dt>Telephone :</dt><dd>604-555-0182</dd>
      <dt>Email:</dt><dd>hello@carewell.ca</dd>
      <dt>Address:</dt><dd>48 Orchard Lane<br>Kelowna,B. Canada,<br>V2B 4KD</dd>
    </dl>
  </div>
</div></footer>

<div class="bottom"><div class="wrap">
  <span>© 2015 Carewell Health. All Rights Reservsd</span>
  <span class="legal"><a href="#">About Us</a><a href="#">Terms of Use</a><a href="#">Privacy Policy</a></span>
  <span class="credit">Site design &amp; developed by Brightline Web Studio</span>
</div></div>
</body>
</html>
```